Building company buisness cards

We are looking for a sharp modern new look for our business cards.
We are a New Zealand based company that specialises in house and land packages.
We have attached a photo of the current logo and would like to see if it can be improved somehow if needed.
We are open to any colours but we have chosen green at this stage.
Feel free to change the font and make the logo smarter looking.
Play with the colours and see what looks best.

We want a card that looks so good know one will want to throw it away!

Target Market(s)

Home buyers

Industry/Entity Type

Building

Contact Information for Business Card

Derek Tolvane
0217394062
dtolvane@quillmarkhomesteads.co.nz
quillmarkhomesteads.co.nz

Font styles to use
Serif
Sans Serif

Colors

Designer to choose colors to be used in the design.

Requirements
Must have
• Logo and company name on one side, details on the other side
Nice to have
• Color codes for the original green are HEX #4a8028, RGB(74,128,40), CMYK(42,0,69,50)
• Round corners, Raised and/or spot UV

```html
<!DOCTYPE html>
<html lang="en">
<head>
<meta charset="utf-8">
<title>Quillmark Homesteads – Business Card</title>
<link href="https://fonts.googleapis.com/css2?family=Open+Sans:wght@400;700&display=swap" rel="stylesheet">
<style>
  :root {
    --stage: #e9e7e3;
    --card: #ffffff;
    --green: #0f8a1c;
    --green-light: #2fa236;
    --green-dark: #06701a;
    --ink: #111111;
    --text: #2e2e2e;
  }
  html, body {
    margin: 0;
    width: 1200px;
    height: 1023px;
    overflow: hidden;
    background: var(--stage);
  }
  .canvas {
    position: relative;
    width: 1200px;
    height: 1023px;
  }
  .business-card {
    position: absolute;
    left: 100px;
    top: 225px;
    width: 1000px;
    height: 572px;
    background: var(--card);
    border-radius: 14px;
    overflow: hidden;
    box-shadow: 0 10px 30px rgba(0,0,0,0.18);
    font-family: "Open Sans", sans-serif;
  }
  .card-swoosh {
    position: absolute;
    inset: 0;
    width: 100%;
    height: 100%;
  }
  .brand {
    position: absolute;
    left: 460px;
    top: 110px;
    display: flex;
    align-items: flex-start;
    gap: 14px;
  }
  .brand-dot {
    width: 22px;
    height: 22px;
    border-radius: 50%;
    background: var(--green);
    margin-top: 10px;
  }
  .brand-name {
    margin: 0;
    color: var(--green);
    font-weight: 700;
    font-size: 32px;
    line-height: 1.15;
    letter-spacing: -0.5px;
  }
  .holder-name {
    position: absolute;
    left: 60px;
    top: 222px;
    margin: 0;
    font-size: 34px;
    font-weight: 400;
    color: var(--ink);
  }
  .contact-list {
    position: absolute;
    left: 60px;
    top: 300px;
    margin: 0;
    padding: 0;
    list-style: none;
  }
  .contact-list li {
    display: flex;
    align-items: center;
    gap: 12px;
    height: 36px;
    font-size: 21px;
    color: var(--text);
  }
  .contact-icon {
    width: 20px;
    height: 20px;
    flex: none;
  }
</style>
</head>
<body>
<main class="canvas">
  <section class="business-card" aria-label="Business card front">
    <svg class="card-swoosh" viewBox="0 0 1000 572" aria-hidden="true">
      <defs>
        <linearGradient id="swooshGreen" x1="0" y1="1" x2="1" y2="0">
          <stop offset="0" stop-color="var(--green-light)"/>
          <stop offset="0.6" stop-color="var(--green)"/>
          <stop offset="1" stop-color="var(--green-dark)"/>
        </linearGradient>
      </defs>
      <path class="swoosh-stripe" fill="var(--ink)"
        d="M40,572 C300,562 540,430 680,260 C770,150 870,55 1000,25 L1000,95 C890,120 810,190 740,290 C610,460 400,562 120,572 Z"/>
      <path class="swoosh-band" fill="url(#swooshGreen)"
        d="M150,572 C420,560 640,440 770,290 C850,195 920,135 1000,118 L1000,572 Z"/>
    </svg>

    <div class="brand">
      <span class="brand-dot"></span>
      <p class="brand-name">Quillmark<br>Homesteads.</p>
    </div>

    <h1 class="holder-name">Derek Tolvane</h1>

    <ul class="contact-list">
      <li>
        <svg class="contact-icon" viewBox="0 0 20 20" aria-hidden="true">
          <rect width="20" height="20" rx="3" fill="var(--green)"/>
          <path d="M6 4.5 L8 4.5 L9 7.5 L7.6 8.6 C8.3 10 9.8 11.6 11.4 12.4 L12.5 11 L15.5 12 L15.5 14 C15.5 15 14.5 15.6 13.5 15.4 C9.2 14.5 5.5 10.8 4.6 6.5 C4.4 5.5 5 4.5 6 4.5 Z" fill="#fff"/>
        </svg>
        <span>0217394062</span>
      </li>
      <li>
        <svg class="contact-icon" viewBox="0 0 20 20" aria-hidden="true">
          <rect width="20" height="20" rx="3" fill="var(--green)"/>
          <rect x="4" y="6" width="12" height="8.5" rx="1" fill="none" stroke="#fff" stroke-width="1.5"/>
          <path d="M4.5 6.5 L10 11 L15.5 6.5" fill="none" stroke="#fff" stroke-width="1.5"/>
        </svg>
        <span>dtolvane@quillmarkhomesteads.co.nz</span>
      </li>
      <li>
        <svg class="contact-icon" viewBox="0 0 20 20" aria-hidden="true">
          <rect width="20" height="20" rx="3" fill="var(--green)"/>
          <circle cx="10" cy="10" r="5.5" fill="none" stroke="#fff" stroke-width="1.4"/>
          <ellipse cx="10" cy="10" rx="2.3" ry="5.5" fill="none" stroke="#fff" stroke-width="1.2"/>
          <path d="M4.5 10 H15.5" stroke="#fff" stroke-width="1.2"/>
        </svg>
        <span>quillmarkhomesteads.co.nz</span>
      </li>
    </ul>
  </section>
</main>
</body>
</html>
```